Book cover for book about Climate Change

Looking for a clean, bold, and attractive cover for a mass-market paperback (5.5"x 8.5") about solving the climate change problem. Title is either "Where the Rivers Meet” or A Harbor Made of Glass” (your choice), subtitle is "A practical field guide to mending the weather — so that the young ones after us inherit steady seasons and open skies," author is Lorne Whitcombe. Thinking that it *might* feature an image of Earth (or a portion thereof) and its very thin layer of atmosphere -- but STRONGLY encourage other ideas too!

Requirements
Nice to have
• Keep it positive — NOT scary doom-and-gloom

```html
<!DOCTYPE html>
<html lang="en">
<head>
<meta charset="utf-8">
<title>A Harbor Made of Glass — Cover Wrap</title>
<link href="https://fonts.googleapis.com/css2?family=Jost:wght@700&family=Lato:ital,wght@0,300;0,400;0,700;1,400;1,900&display=swap" rel="stylesheet">
<style>
  :root {
    --space: #0b0a10;
    --ink-white: #ffffff;
    --ocean-deep: #1b4f9a;
    --ocean-teal: #1f8c74;
    --land-olive: #8e8a4c;
    --land-sand: #cbb48a;
    --cloud: #eceae4;
    --atmosphere: #3d7fe0;
  }
  * { margin: 0; padding: 0; box-sizing: border-box; }
  html, body { width: 1200px; height: 850px; overflow: hidden; background: var(--space); }
  .cover-wrap { position: relative; width: 1200px; height: 850px; background: var(--space); overflow: hidden; }
  .earth-art { position: absolute; inset: 0; width: 1200px; height: 850px; }

  .spine { position: absolute; top: 26px; left: 562px; writing-mode: vertical-rl; color: var(--ink-white); font-family: 'Lato', sans-serif; }
  .spine-title { font-family: 'Jost', sans-serif; font-weight: 700; font-size: 29px; line-height: 34px; text-transform: uppercase; letter-spacing: 0.5px; }
  .spine-subtitle { font-weight: 300; font-size: 10.5px; line-height: 15px; text-transform: uppercase; letter-spacing: 0.2px; }
  .spine-author { position: absolute; top: 652px; left: 578px; writing-mode: vertical-rl; color: var(--ink-white); font-family: 'Lato', sans-serif; font-weight: 400; font-size: 19px; line-height: 30px; letter-spacing: 9px; text-transform: uppercase; }

  .front-author { position: absolute; top: 22px; right: 237px; text-align: right; color: var(--ink-white); font-family: 'Lato', sans-serif; font-weight: 400; font-size: 25px; line-height: 46px; letter-spacing: 15px; text-transform: uppercase; text-shadow: 0 1px 4px rgba(0,0,0,0.35); }
  .front-title { position: absolute; top: 8px; right: 12px; text-align: right; color: var(--ink-white); font-family: 'Jost', sans-serif; font-weight: 700; font-size: 128px; line-height: 106px; letter-spacing: -2px; text-transform: uppercase; text-shadow: 0 2px 8px rgba(0,0,0,0.35); }
  .front-subtitle { position: absolute; top: 682px; left: 700px; width: 450px; text-align: center; color: var(--ink-white); font-family: 'Lato', sans-serif; font-style: italic; font-weight: 400; font-size: 20px; line-height: 27px; text-transform: uppercase; }
  .front-subtitle strong { font-weight: 900; font-size: 27px; }
</style>
</head>
<body>
<main class="cover-wrap">
  <svg class="earth-art" viewBox="0 0 1200 850" aria-hidden="false">
    <defs>
      <linearGradient id="earth-tones" x1="0" y1="0" x2="0.75" y2="1">
        <stop offset="0" stop-color="var(--ocean-deep)"/>
        <stop offset="0.22" stop-color="var(--ocean-teal)"/>
        <stop offset="0.38" stop-color="var(--land-olive)"/>
        <stop offset="0.52" stop-color="var(--land-sand)"/>
        <stop offset="0.72" stop-color="var(--cloud)"/>
        <stop offset="1" stop-color="#dfe4ea"/>
      </linearGradient>
      <filter id="glow-blur" x="-10%" y="-10%" width="120%" height="120%">
        <feGaussianBlur stdDeviation="5"/>
      </filter>
    </defs>
    <path class="atmosphere-glow" d="M0,682 Q780,690 1200,385" fill="none" stroke="var(--atmosphere)" stroke-width="10" filter="url(#glow-blur)"/>
    <path class="earth-photo" role="img" aria-label="Satellite photograph of Earth's curve from orbit: blue-green sea, tan deserts and mountains, white cloud cover, thin blue atmosphere" d="M0,0 H1200 V385 Q780,690 0,682 Z" fill="url(#earth-tones)"/>
  </svg>

  <div class="spine">
    <div class="spine-title">A Harbor Made of Glass</div>
    <div class="spine-subtitle">A practical field guide to mending the weather — so that the young<br>ones after us inherit steady seasons and open skies</div>
  </div>
  <div class="spine-author">Lorne<br>Whitcombe</div>

  <div class="front-author">Lorne<br>Whitcombe</div>
  <h1 class="front-title">A<br>Harbor<br>Made of<br>Glass</h1>
  <p class="front-subtitle">A <strong>practical field guide</strong> to mending<br>the weather — so that the young<br>ones after us inherit steady<br>seasons and open skies</p>
</main>
</body>
</html>
```